Stylish Business Cards Wanted

- DOUBLE SIDED Design Required -

High end, edgy cards for a corporate and personal stylist. Must include logo,
Name: Belinda Harwick
Title: Director and Stylist
telephone : +61 8 7142 5809
email: belinda@theloombriefing.example
website: theloombriefing.example
Tag: Corporate Workwear & Uniform Specialist | Personal Stylist
Would like nice icons for telephone, email, website

Target Market(s)

Businesses wanting stylish uniforms, people wanting stylish wardrobes

Industry/Entity Type

Corporate Workwear Stylist

Contact Information for Business Card

I would like black, white and gold foiling incorporated in the design - possibly a touch of the other colours on my branding guide attached Name: Belinda Harwick Title: Director and Stylist telephone : +61 8 7142 5809 email: belinda@theloombriefing.example website: theloombriefing.example Tag: Corporate Workwear & Uniform Specialist | Personal Stylist Would like nice icons for telephone, email, website

Font styles to use
Other font styles liked:
• Raleway

Colors

Designer to choose colors to be used in the design.

Requirements
Must have
• Gold foil accents

```html
<!DOCTYPE html>
<html lang="en">
<head>
<meta charset="utf-8">
<title>The Loom Briefing – Business Card</title>
<link rel="stylesheet" href="https://fonts.googleapis.com/css2?family=Great+Vibes&family=Raleway:wght@400;500;600&display=swap">
<style>
  :root {
    --backdrop: #8a8a8a;
    --card: #3a3a3c;
    --card-shade: #333335;
    --white: #ececec;
    --soft: #cfcfcf;
    --gold: #d9a530;
    --rule: #8c8c8e;
  }
  * { margin: 0; padding: 0; box-sizing: border-box; }
  html, body {
    width: 1200px;
    height: 904px;
    overflow: hidden;
    background: var(--backdrop);
  }
  .card {
    position: absolute;
    left: 150px;
    top: 202px;
    width: 900px;
    height: 500px;
    background: linear-gradient(160deg, var(--card) 0%, var(--card-shade) 100%);
    border-bottom: 3px solid var(--gold);
    font-family: "Raleway", sans-serif;
    color: var(--soft);
  }
  .holder-name {
    position: absolute;
    left: 72px;
    top: 92px;
    font-family: "Great Vibes", cursive;
    font-size: 74px;
    line-height: 1;
    color: var(--white);
    white-space: nowrap;
  }
  .holder-title {
    position: absolute;
    left: 60px;
    top: 156px;
    font-size: 21px;
    font-weight: 500;
    color: var(--gold);
  }
  .divider {
    position: absolute;
    left: 56px;
    top: 200px;
    width: 590px;
    height: 1px;
    background: var(--rule);
  }
  .contact-list {
    position: absolute;
    left: 40px;
    top: 218px;
    list-style: none;
  }
  .contact-list li {
    display: flex;
    align-items: center;
    gap: 14px;
    font-size: 20px;
    line-height: 34px;
    color: var(--soft);
  }
  .contact-list svg { width: 18px; height: 18px; flex: none; }
  .brand {
    position: absolute;
    right: 70px;
    top: 176px;
    display: flex;
    align-items: center;
    gap: 12px;
  }
  .brand-mark {
    width: 14px;
    height: 14px;
    background: var(--gold);
  }
  .brand-name {
    font-size: 34px;
    font-weight: 500;
    letter-spacing: 2px;
    color: var(--white);
    white-space: nowrap;
  }
  .tag-rule {
    position: absolute;
    right: 60px;
    top: 352px;
    width: 270px;
    height: 1px;
    background: var(--rule);
  }
  .tag-list {
    position: absolute;
    right: 60px;
    top: 366px;
    list-style: none;
    text-align: right;
  }
  .tag-list li {
    font-size: 20px;
    line-height: 30px;
    color: var(--soft);
  }
  .tag-list li::after {
    content: "";
    display: inline-block;
    width: 9px;
    height: 9px;
    margin-left: 12px;
    border-radius: 50%;
    background: var(--gold);
    vertical-align: middle;
  }
</style>
</head>
<body>
  <main class="card">
    <p class="holder-name">Belinda Harwick</p>
    <p class="holder-title">Director &amp; Stylist</p>
    <div class="divider"></div>
    <ul class="contact-list">
      <li>
        <svg viewBox="0 0 24 24" fill="none" stroke="#d9a530" stroke-width="2" stroke-linejoin="round">
          <path d="M5 3h4l2 5-2.5 1.5a11 11 0 0 0 6 6L16 13l5 2v4a2 2 0 0 1-2 2A16 16 0 0 1 3 5a2 2 0 0 1 2-2z"/>
        </svg>
        +61 8 7142 5809
      </li>
      <li>
        <svg viewBox="0 0 24 24" fill="none" stroke="#d9a530" stroke-width="2" stroke-linejoin="round">
          <rect x="3" y="5" width="18" height="14" rx="1"/>
          <path d="M3 6l9 7 9-7"/>
        </svg>
        belinda@theloombriefing.example
      </li>
      <li>
        <svg viewBox="0 0 24 24" fill="none" stroke="#d9a530" stroke-width="2">
          <circle cx="12" cy="12" r="9"/>
          <path d="M3 12h18M12 3c3 3 3 15 0 18M12 3c-3 3-3 15 0 18"/>
        </svg>
        theloombriefing.example
      </li>
    </ul>
    <div class="brand">
      <span class="brand-mark"></span>
      <span class="brand-name">The Loom Briefing</span>
    </div>
    <div class="tag-rule"></div>
    <ul class="tag-list">
      <li>Corporate Workwear</li>
      <li>Uniform Specialist</li>
      <li>Personal Stylist</li>
    </ul>
  </main>
</body>
</html>
```